New Design for our Velostine Gran Reserva Brandy, it is the label design for the bottle label

We need a new bottle label for our Brandy Gran Reserva that we want to bring to the market.

Please have a look at all our current bottles and labels and the feel of our company under www.velostine-example.ch

The bottle that we will be using for the brand is a different one than the one that we already have, the design of the bottle is attached with a document.

I have also attached a briefing in regards to Brandy in general for your information.

### 1. What is Brandy?
Brandy is a distilled spirit made from fermented wine or other fruit wines. It is traditionally aged in oak barrels, which gives it its characteristic color and rich flavor. The aging process in oak is essential for developing the aromas and quality of the brandy.

### 2. What is Brandy Reserva?
A Brandy labeled as "Reserva" has undergone a longer aging process, typically at least 2 to 3 years, in oak barrels. This aging gives the brandy a deeper, more complex flavor profile and a darker color. "Reserva" is often an indication of higher quality.

### 3. Who enjoys drinking Brandy?
Brandy is typically favored by those who appreciate a deep, rich tasting experience. This often includes older consumers who value the time-aged complexity of the spirit. However, Brandy is also gaining popularity among younger people, especially through cocktails and modern serving styles.

### 4. Why is Brandy trending?
Brandy is experiencing a resurgence as consumers increasingly value quality and artisanal production methods. Its versatility in cocktails and association with traditional, luxurious experiences have also contributed to its renewed popularity.

### 5. What colors would be associated with Brandy?
The typical colors associated with Brandy are warm gold, amber, and deep golden-brown tones. These colors reflect the aging process in oak barrels and the richness of the flavors. Other associated colors might include dark brown and mahogany.

### 6. What is important to customers when buying Brandy?
Customers care about the origin of the Brandy, the aging time, the quality of the ingredients, the production method, and the brand. They also pay attention to the prestige of the product and the authenticity of the production.

### 7. What is not important to customers when buying Brandy?
For many customers, the price and packaging (unless it’s especially exclusive) may be less important than the quality and taste of the Brandy. The distillery name might be less significant if it isn’t tied to a particular reputation.

### 8. What do customers know about Swiss Brandy?
Swiss Brandy is still relatively unknown in many markets, but customers who are familiar with it appreciate the precision and quality of Swiss production. Swiss Brandy is assumed to be made with care and under strict quality standards.

### 9. What is Brandy Gran Reserva?
**Brandy Gran Reserva** is an even higher quality and longer-aged version of Brandy. Generally, a Gran Reserva is aged for at least 5 to 10 years or more in oak barrels. This extended aging process gives the Brandy an especially deep, complex flavor profile and often a darker, richer color. Gran Reserva is often regarded as the top-tier product within a Brandy range and appeals to discerning consumers who value quality, refinement, and a luxurious tasting experience.

The label “Gran Reserva” thus indicates the highest quality level for Brandies, similar to other spirits (like wine or whisky), where the aging time is a critical factor.

### 10. What emotions are associated with Brandy?
Brandy is often associated with luxury, relaxation, and comfort. It evokes feelings of tradition, elegance, and sophistication. Drinking Brandy is frequently seen as a moment of reflection and enjoyment.

### 11. How should Brandy be marketed?
Brandy should be marketed with a focus on its artisanal production, quality, and tradition. A narrative around the product, its aging, and origin can help create an emotional connection with the customer. The marketing should also emphasize the versatility of Brandy, whether consumed neat or in cocktails.

### 12. Sales test and label design for Velostine Brandy
For a sales test, I would suggest a tasting in an upscale setting, perhaps paired with a storytelling presentation highlighting the history of the 6-year aged Brandy and its aging in oak barrels.

**Label design**:
The label should reflect the exclusivity of the product, with an elegant, minimalist design. Colors like deep gold, mahogany, and a hint of deep blue could be used to emphasize the aging and quality of the Brandy. The label should include information about the aging time, the use of oak barrels, and a brief story about the Brandy’s production. A seal or embossing highlighting the craftsmanship would also be fitting.

Target Market(s)

Customers that like Brandy

Requirements
Must have
• the Alcohol % must be included on the label as well as our address.

```html
<!DOCTYPE html>
<html lang="en">
<head>
<meta charset="utf-8">
<title>Velostine Gran Reserva Brandy – Label Set</title>
<link rel="stylesheet" href="https://fonts.googleapis.com/css2?family=Cinzel:wght@400;600;700&family=Cormorant+Garamond:ital,wght@0,500;0,600;1,400&family=Pinyon+Script&display=swap">
<style>
  :root {
    --page: #ffffff;
    --green: #0b2a20;
    --black-band: #151615;
    --gold: #b8913f;
    --gold-dark: #9a7633;
    --cream: #f1ede3;
    --ink: #3c3a36;
    --silver: #d3d6d4;
    --seal: #a3161b;
    --flag: #d52b1e;
  }
  html, body {
    margin: 0;
    padding: 0;
    width: 1200px;
    height: 1200px;
    overflow: hidden;
    background: var(--page);
  }
  .canvas {
    position: relative;
    width: 1200px;
    height: 1200px;
  }
  .neck-strip {
    position: absolute;
    left: 554px;
    top: 92px;
    width: 92px;
    height: 382px;
  }
  .main-label {
    position: absolute;
    left: 321px;
    top: 502px;
    width: 558px;
    height: 607px;
  }
  .caps { font-family: "Cinzel", serif; }
  .script { font-family: "Pinyon Script", cursive; }
  .body-serif { font-family: "Cormorant Garamond", serif; }
  .brand-name { font-family: "Cinzel", serif; font-weight: 700; fill: #ffffff; }
  .product-title { font-family: "Cinzel", serif; font-weight: 700; fill: var(--gold); letter-spacing: 2px; }
  .gold-caps { font-family: "Cinzel", serif; font-weight: 700; fill: var(--gold); }
  .ink-caps { font-family: "Cinzel", serif; font-weight: 700; fill: #1d1d1b; }
  .grey-caps { font-family: "Cinzel", serif; font-weight: 600; fill: #6d6a63; letter-spacing: 1px; }
  .story { font-family: "Cormorant Garamond", serif; font-style: italic; fill: #5a564e; }
  .note { font-family: "Cormorant Garamond", serif; font-style: italic; fill: #5a564e; }
  .note-key { font-weight: 600; fill: #3c3a36; }
  .age-number { font-family: "Cormorant Garamond", serif; font-weight: 600; fill: var(--ink); }
</style>
</head>
<body>
<main class="canvas">

  <!-- Neck strip -->
  <svg class="neck-strip" viewBox="0 0 102 424" role="group" aria-label="Neck strip label">
    <defs>
      <pattern id="neck-teeth" width="6" height="6" patternUnits="userSpaceOnUse">
        <path d="M0 6 L3 0 L6 6 Z" fill="var(--cream)"/>
      </pattern>
      <clipPath id="neck-shape"><rect width="102" height="424" rx="5"/></clipPath>
      <clipPath id="neck-script-area"><rect x="4" y="8" width="94" height="288"/></clipPath>
    </defs>
    <g clip-path="url(#neck-shape)">
      <rect class="neck-dark" width="102" height="424" fill="var(--green)"/>
      <rect class="neck-panel" y="306" width="102" height="118" fill="var(--cream)"/>
      <rect class="neck-edge" y="300" width="102" height="6" fill="url(#neck-teeth)"/>
    </g>
    <g clip-path="url(#neck-script-area)">
      <text class="script" transform="translate(64 170) rotate(-80)" text-anchor="middle" font-size="46" fill="var(--silver)">Brandy</text>
    </g>
    <text class="ink-caps" x="51" y="335" text-anchor="middle" font-size="14">Grand</text>
    <text class="ink-caps" x="51" y="352" text-anchor="middle" font-size="14">Reserva</text>
    <text class="ink-caps" x="51" y="369" text-anchor="middle" font-size="10">Very Special</text>
    <text class="ink-caps" x="51" y="382" text-anchor="middle" font-size="10">Pot Still</text>
    <text class="ink-caps" x="51" y="395" text-anchor="middle" font-size="10">Brandy</text>
  </svg>

  <!-- Main front label -->
  <svg class="main-label" viewBox="0 0 620 675" role="group" aria-label="Front bottle label">
    <defs>
      <pattern id="panel-teeth-top" width="6" height="6" patternUnits="userSpaceOnUse" x="82">
        <path d="M0 6 L3 0 L6 6 Z" fill="var(--cream)"/>
      </pattern>
      <pattern id="panel-teeth-bottom" width="6" height="6" patternUnits="userSpaceOnUse" x="82">
        <path d="M0 0 L3 6 L6 0 Z" fill="var(--cream)"/>
      </pattern>
      <clipPath id="label-shape"><rect width="620" height="675" rx="12"/></clipPath>
    </defs>

    <g clip-path="url(#label-shape)">
      <rect class="label-ground" width="620" height="675" fill="var(--green)"/>
      <rect class="header-band" width="620" height="166" fill="var(--black-band)" role="img" aria-label="Dark ornamental lattice pattern"/>
      <rect class="gold-rule" y="166" width="620" height="3" fill="var(--gold)"/>
    </g>

    <!-- Brand header -->
    <rect class="origin-mark" x="296" y="31" width="28" height="16" fill="var(--flag)"/>
    <text class="brand-name" x="310" y="98" text-anchor="middle" font-size="36">Velostine</text>
    <text class="caps" x="310" y="124" text-anchor="middle" font-size="10" fill="#e6e6e6" letter-spacing="1">Swiss Distillery</text>

    <!-- Product name -->
    <text class="script" x="305" y="285" text-anchor="middle" font-size="96" fill="var(--silver)">Brandy</text>
    <text class="product-title" x="310" y="358" text-anchor="middle" font-size="30">Gran Reserva</text>
    <text class="gold-caps" x="310" y="374" text-anchor="middle" font-size="12" letter-spacing="1">Very Special Pot Still Brandy</text>

    <!-- Information panel -->
    <rect class="info-panel" x="82" y="426" width="455" height="158" fill="var(--cream)"/>
    <rect x="82" y="420" width="455" height="6" fill="url(#panel-teeth-top)"/>
    <rect x="82" y="584" width="455" height="6" fill="url(#panel-teeth-bottom)"/>

    <g class="story" font-size="9">
      <text x="107" y="449">This brandy is crafted from carefully selected</text>
      <text x="107" y="464">grapes, distilled in Copper Pot Stills, and aged for</text>
      <text x="107" y="479">at least 6 years in French Oak Barrels. The long</text>
      <text x="107" y="494">aging process allows the Brandy to develop</text>
      <text x="107" y="509">complex flavors and a smooth, rich character.</text>
    </g>

    <g class="age-mark">
      <text class="gold-caps" x="309" y="452" text-anchor="middle" font-size="11" letter-spacing="1">Aged</text>
      <text class="age-number" x="309" y="496" text-anchor="middle" font-size="50">6</text>
      <text class="gold-caps" x="309" y="509" text-anchor="middle" font-size="11" letter-spacing="1">Years</text>
      <line x1="285" y1="514" x2="333" y2="514" stroke="var(--gold)" stroke-width="0.8"/>
    </g>

    <g class="note" font-size="8.5">
      <text x="353" y="455"><tspan class="note-key">Colour:</tspan> rich golden colour</text>
      <line x1="353" y1="460" x2="510" y2="460" stroke="#d8d2c3" stroke-width="0.6"/>
      <text x="353" y="471"><tspan class="note-key">Aroma:</tspan> ripe apple with hints of vanilla</text>
      <line x1="353" y1="476" x2="510" y2="476" stroke="#d8d2c3" stroke-width="0.6"/>
      <text x="353" y="487"><tspan class="note-key">Taste:</tspan> spicy with fruity palate</text>
      <line x1="353" y1="492" x2="510" y2="492" stroke="#d8d2c3" stroke-width="0.6"/>
      <text x="353" y="503"><tspan class="note-key">Finish:</tspan> well balanced with a fruity aftertaste</text>
    </g>

    <g class="barrel-line">
      <text class="grey-caps" x="285" y="544" text-anchor="end" font-size="10">Aged In French</text>
      <rect x="293" y="526" width="32" height="30" rx="8" fill="#a9a69f" role="img" aria-label="Stacked oak barrels icon"/>
      <text class="grey-caps" x="333" y="544" font-size="10">Oak Barrels</text>
    </g>
    <text class="gold-caps" x="310" y="574" text-anchor="middle" font-size="9" letter-spacing="1">45% Alc. Vol.  |  750 ml</text>

    <circle class="wax-seal" cx="497" cy="562" r="40" fill="var(--seal)" role="img" aria-label="Red wax seal, hand-crafted small batch"/>

    <text class="gold-caps" x="310" y="634" text-anchor="middle" font-size="9" letter-spacing="1" fill="var(--gold-dark)">Produced by Velostine Swiss Distillery, Switzerland</text>
  </svg>

</main>
</body>
</html>
```